Plenko - Shoe Fitting App : Foot scanning app, 3D reconstruction and Fit recommandation.

We are a startup that has developed a 3D scanning App that compares the 3d reconstructed foot to the 3D Last (mould) of a shoe to find the best match and recommend a shoe size with a graphical representation of the fit on a reconstructed foot without texturing. The challenge of this app is to have a simple and intuitive onboarding of the user with clean and crisp ui and a simple tutorial for foot scanning. 3D representation of the fit is also key. What you see is what you feel is what we would like to achieve.

Target Market(s)

Sneaker Brands and athletic shoes brands

Industry/Entity Type

Footwear

Font styles to use
Other font styles liked:
• Oswald or Droid Serif

Colors
0094D4
00A9DD
6FCCEA
C7EBF8
E9F6FB

Requirements
Must have
• Simple intuitive UI to onboard the customer to scan his bare foot (please look at attached image on how to scan the foot). You must flip your phone so that the screen is facing your foot. Start at 40cm distance form the front of your foot and turn 360% slowly to capture the foot while you feel the aptic of the iPhone. That needs to be presented with a simple animation that the user can easily understand and skip if he is a returning customer and knows how to do that. the rest of the UI is to present the result of the scanned foot for the user to use to get his fit and size. The other must have is the final result screen. Where the user will a representation of the foot (snug, loose ) of different predefined areas of the foot so he can choose the fit that he likes and not necessarily the size that we suggest. Must match website design (https://www.plenko.example)
Nice to have
• An animation of the whole process (scan-compare 3d foot with 3d shoe last(or mould) and get the 3D result of the best fit + associated size. Optionaly, an option to play with your foot and transform it (avatar like with accessories and colours)
Should not have
• Too many colours. Too much text. No gender type. No race type.

```html
<!DOCTYPE html>
<html lang="en">
<head>
<meta charset="utf-8">
<title>Plenko – Foot Scan Onboarding Screens</title>
<link href="https://fonts.googleapis.com/css2?family=Montserrat:wght@400;500;600;700;800&display=swap" rel="stylesheet">
<style>
  :root {
    --canvas: #ffffff;
    --screen: #000000;
    --ink: #ffffff;
    --ink-soft: #e6e6e6;
    --track: #0d0d0d;
    --track-line: #2a2a2a;
    --btn-ink: #000000;
    --glow: #d9c21a;
    --glow-deep: #c77a12;
    --skin: #c9a48d;
    --mesh: #6fd6b0;
    --wire: #8a8a8a;
  }
  * { box-sizing: border-box; margin: 0; padding: 0; }
  html, body { width: 1039px; height: 1200px; overflow: hidden; background: var(--canvas); }
  body { font-family: "Montserrat", sans-serif; color: var(--ink); position: relative; }

  .screen { position: absolute; width: 284px; height: 506px; background: var(--screen); overflow: hidden; }
  .screen--light { left: 68px; top: 74px; }
  .screen--undress { left: 387px; top: 76px; }
  .screen--flip { left: 700px; top: 74px; }
  .screen--check-a { left: 68px; top: 620px; border-radius: 28px; }
  .screen--check-b { left: 378px; top: 613px; }
  .screen--loading { left: 700px; top: 619px; }

  .wordmark { position: absolute; left: 0; right: 0; text-align: center; font-weight: 800; font-size: 38px; letter-spacing: 1px; line-height: 1; }
  .wordmark--small { font-size: 30px; }

  .headline { position: absolute; left: 20px; right: 20px; text-align: center; font-weight: 700; font-size: 18.5px; line-height: 22px; text-transform: uppercase; }
  .lede { position: absolute; left: 28px; right: 28px; text-align: center; font-size: 9.4px; line-height: 13.4px; color: var(--ink-soft); }
  .prompt { position: absolute; left: 16px; right: 16px; text-align: center; font-weight: 600; font-size: 11.6px; line-height: 17px; }

  .pill { position: absolute; background: var(--ink); color: var(--btn-ink); border-radius: 20px; display: flex; align-items: center; justify-content: center; font-weight: 800; }
  .pill--next { left: 73px; top: 428px; width: 132px; height: 32px; font-size: 11.5px; justify-content: space-between; padding: 0 20px 0 22px; letter-spacing: .3px; }
  .pill--foot { left: 168px; top: 449px; width: 95px; height: 32px; font-size: 12px; }
  .pill--half { top: 449px; width: 113px; height: 32px; font-size: 11.5px; }
  .pill--results { left: 25px; top: 448px; width: 234px; height: 31px; font-size: 12px; gap: 10px; }

  .dots { position: absolute; left: 0; width: 284px; top: 474px; display: flex; justify-content: center; gap: 5px; padding-right: 6px; }
  .dot { width: 5px; height: 5px; border-radius: 50%; border: 1px solid var(--ink); }
  .dot--on { background: var(--ink); }

  .art { position: absolute; }
  .art--bulb { left: 70px; top: 225px; width: 150px; height: 175px; background: radial-gradient(ellipse at 50% 42%, #fff7c9 0%, var(--glow) 18%, rgba(199,122,18,.55) 34%, rgba(80,60,0,.2) 55%, transparent 72%); }
  .art--legs { left: 89px; top: 232px; width: 99px; height: 168px; background: linear-gradient(180deg, #1a1a1a, #2b2b2b); border-radius: 30px 30px 14px 14px; }
  .art--boots { left: 36px; top: 325px; width: 34px; height: 32px; background: #3a3a3a; border-radius: 4px; }
  .art--socks { left: 203px; top: 325px; width: 33px; height: 35px; background: #3a3a3a; border-radius: 4px; }
  .art--wire { left: 77px; top: 193px; width: 151px; height: 232px; background: radial-gradient(ellipse at 55% 55%, #3c3c3c 0%, #1c1c1c 55%, transparent 80%); }
  .art--foot { left: 34px; top: 164px; width: 209px; height: 180px; background: linear-gradient(160deg, var(--skin) 0%, #b78f7a 55%, var(--mesh) 100%); border-radius: 60% 30% 45% 40% / 30% 20% 70% 60%; opacity: .9; }

  .eye { position: absolute; left: 126px; top: 390px; width: 32px; height: 20px; }

  .caption { position: absolute; left: 0; right: 0; text-align: center; }
  .title-md { font-weight: 600; font-size: 15px; line-height: 18px; }
  .title-sm { font-weight: 800; font-size: 11px; line-height: 14px; letter-spacing: .2px; }
  .copy { font-size: 9px; line-height: 13.4px; color: var(--ink-soft); }

  .progress { position: absolute; left: 17px; width: 253px; height: 19px; border-radius: 8px; font-size: 5.5px; display: flex; align-items: center; padding: 0 10px; }
  .progress--empty { top: 95px; background: var(--track); border: 1px solid var(--track-line); color: var(--ink); }
  .progress--full { top: 211px; background: var(--ink); color: var(--btn-ink); justify-content: flex-end; }

  .segmented { position: absolute; left: 25px; top: 297px; width: 234px; height: 31px; border: 1.5px solid var(--ink); border-radius: 16px; display: flex; align-items: center; font-size: 9.6px; }
  .segment { flex: 1; text-align: center; }
  .segment--on { background: var(--ink); color: var(--btn-ink); font-weight: 700; border-radius: 14px; height: 100%; display: flex; align-items: center; justify-content: center; flex: 0 0 76px; }
</style>
</head>
<body>

<section class="screen screen--light">
  <div class="wordmark" style="top:26px">Plenko</div>
  <h2 class="headline" style="top:88px">Make sure<br>you're in a well<br>lit area</h2>
  <p class="lede" style="top:167px">Avoid strong light from only one direction. This casts deep shadows that reduce accuracy of the scan.</p>
  <div class="art art--bulb" role="img" aria-label="Glowing yellow light bulb illustration"></div>
  <div class="pill pill--next">NEXT
    <svg width="22" height="10" viewBox="0 0 22 10"><path d="M0 5H20M15 1L20 5L15 9" stroke="#000" stroke-width="1.8" fill="none"/></svg>
  </div>
  <div class="dots"><span class="dot dot--on"></span><span class="dot"></span><span class="dot"></span></div>
</section>

<section class="screen screen--undress">
  <div class="wordmark" style="top:27px">Plenko</div>
  <h2 class="headline" style="top:89px">Take off your<br>shoes and roll<br>up pants</h2>
  <p class="lede" style="top:168px">To scan your feet, the camera needs to see the unique details, including your ankle.</p>
  <div class="art art--legs" role="img" aria-label="Line drawing of bare lower legs and feet"></div>
  <div class="art art--boots" role="img" aria-label="Boots icon"></div>
  <div class="art art--socks" role="img" aria-label="Socks icon"></div>
  <div class="pill pill--next">NEXT
    <svg width="22" height="10" viewBox="0 0 22 10"><path d="M0 5H20M15 1L20 5L15 9" stroke="#000" stroke-width="1.8" fill="none"/></svg>
  </div>
  <div class="dots"><span class="dot"></span><span class="dot dot--on"></span><span class="dot"></span></div>
</section>

<section class="screen screen--flip">
  <div class="wordmark" style="top:26px">Plenko</div>
  <h2 class="headline" style="top:88px">Flip the screen<br>towards your<br>toes to start<br>scanning</h2>
  <div class="art art--wire" role="img" aria-label="Grey wireframe mesh of an ankle and foot"></div>
  <div class="pill pill--foot">Right Foot</div>
</section>

<section class="screen screen--check-a">
  <div class="wordmark" style="top:36px">Plenko</div>
  <p class="prompt" style="top:100px">Please check that the reconstruction<br>of your foot seems correct.</p>
  <div class="art art--foot" style="top:172px" role="img" aria-label="3D reconstructed bare foot with green mesh overlay"></div>
  <svg class="eye" style="top:390px" viewBox="0 0 32 20" aria-hidden="true"><path d="M1 10C6 2 26 2 31 10C26 18 6 18 1 10Z" fill="#fff"/><circle cx="16" cy="10" r="6" fill="#000"/><circle cx="17" cy="9" r="3.6" fill="#fff"/><circle cx="18.3" cy="9" r="3" fill="#000"/></svg>
  <div class="pill pill--half" style="left:21px">Scan Again</div>
  <div class="pill pill--half" style="left:150px">My Fit</div>
</section>

<section class="screen screen--check-b">
  <div class="wordmark" style="top:30px">Plenko</div>
  <p class="prompt" style="top:94px">Please check that the reconstruction<br>of your foot seems correct.</p>
  <div class="art art--foot" role="img" aria-label="3D reconstructed bare foot with green mesh overlay"></div>
  <svg class="eye" viewBox="0 0 32 20" aria-hidden="true"><path d="M1 10C6 2 26 2 31 10C26 18 6 18 1 10Z" fill="#fff"/><circle cx="16" cy="10" r="6" fill="#000"/><circle cx="17" cy="9" r="3.6" fill="#fff"/><circle cx="18.3" cy="9" r="3" fill="#000"/></svg>
  <div class="pill pill--half" style="left:21px">Scan Again</div>
  <div class="pill pill--half" style="left:147px">My Fit</div>
</section>

<section class="screen screen--loading">
  <div class="wordmark wordmark--small" style="top:16px">Plenko</div>
  <h2 class="caption title-md" style="top:58px">LOADING YOUR DATA</h2>
  <p class="caption copy" style="top:75px">This process might take a few minutes.</p>
  <div class="progress progress--empty">0%</div>
  <h3 class="caption title-sm" style="top:124px">FUN FACTS ABOUT FEET</h3>
  <p class="caption copy" style="top:142px">Our feet have nearly a quarter of all the bones in<br>our bodies — each one has 26 bones.</p>
  <h3 class="caption title-sm" style="top:185px">YOU’RE ALL MEASURED UP</h3>
  <div class="progress progress--full">100%</div>
  <h3 class="caption title-sm" style="top:248px">TELL US YOUR PREFERENCE</h3>
  <p class="caption copy" style="top:267px">How do your prefer the cushion?</p>
  <div class="segmented">
    <span class="segment">Soft</span>
    <span class="segment segment--on">Medium</span>
    <span class="segment">Hard</span>
  </div>
  <p class="caption copy" style="top:348px">Select an option to go to the next<br>personal preferences setting</p>
  <p class="caption copy" style="top:390px; left:24px; right:24px">Click below to see how this shoe fits. Now that you're scanned, you can quickly try other shoes without going through the process again.</p>
  <div class="pill pill--results">SEE RESULTS
    <svg width="22" height="10" viewBox="0 0 22 10"><path d="M0 5H20M15 1L20 5L15 9" stroke="#000" stroke-width="1.8" fill="none"/></svg>
  </div>
</section>

</body>
</html>
```